Healthcare/Medical Consultant Company

QRN is a Healthcare Conultant Company. We help doctors manage the business side of their medical practice.
We already have a very basic world press design. We want an upgraded design that conveys partnership, healthcare expertise and healthcare innovation to our client. It needs to have a sleek, clean, modern and inclusive look. Pictures need need to convey diversity (including pictures of people of all races and shows both men and women working together in a healthcare environment to make it better). The Pictures on the home page should particularly illustrate diversity and Healthcare expertise. The company logo is blue and white but the site doesn’t have to follow the exact same theme but the logo needs to blend well with the chosen theme. The logo should ideally be in the header of the website. We would also like the following included in our website:

1. Pages should include: a home page, About Us page, Services page, Get a quote page, Contact Us page, Staff page(where we can add pictures and bio for staff).

2. The Drop down menu for services should have hyperlinks ( for each service)Leading to a page that provides detailed info about that specific service. Our services include: Revenue Cycle Management, Regulatory Compliance, Human Resources Management, & practice Management.

3. Links to social media should in the header or footer of each page.

4. Contact info should be in the footer of each page.

5. Clients should be an email to us from the contact page.

Target Market(s)

Physician Medical Practices

Industry/Entity Type

Medical

Coding

Coded - Design and coding required

Font styles to use
Sans Serif

Colors

Designer to choose colors to be used in the design.

Requirements
Must have
• See project description
Nice to have
• See project description

```html
<!DOCTYPE html>
<html lang="en">
<head>
<meta charset="utf-8">
<title>QRN Health Partners LLC</title>
<link href="https://fonts.googleapis.com/css2?family=Merriweather:wght@400;700&family=Roboto:wght@300;400;500&display=swap" rel="stylesheet">
<style>
:root{
  --blue:#0d55a5;
  --blue-dark:#0a4a94;
  --sky:#2b9bd6;
  --ink:#333;
  --grey:#888;
  --light:#f1f1f1;
  --dark:#333333;
  --darker:#1c1c1c;
  --white:#fff;
}
*{margin:0;padding:0;box-sizing:border-box}
html,body{width:1200px;height:2899px;overflow:hidden;background:var(--white)}
body{font-family:'Roboto',sans-serif;color:var(--ink)}
.page{position:relative;width:1200px;height:2899px;overflow:hidden}
.abs{position:absolute}

/* header */
.header{left:0;top:0;width:1200px;height:114px;background:var(--white);border-bottom:3px solid #e6e6e6}
.brand{left:77px;top:14px;display:flex;flex-direction:column;align-items:center;gap:4px}
.brand-name{font-family:'Merriweather',serif;font-weight:700;font-size:58px;color:var(--blue);letter-spacing:4px;line-height:1}
.brand-full{font-family:'Merriweather',serif;font-size:16px;color:#222}
.nav{left:473px;top:35px;display:flex;align-items:center}
.nav a{display:block;font-size:14px;color:#aaa;text-decoration:none;padding:0 24px;line-height:42px;text-transform:uppercase}
.nav a.active{background:var(--blue);color:var(--white);padding:0 25px}

/* hero */
.hero-photo{left:0;top:116px;width:1200px;height:628px;
  background:
    linear-gradient(180deg,rgba(255,255,255,0) 0%,rgba(255,255,255,0) 80%,rgba(200,205,210,.55) 100%),
    linear-gradient(90deg,#c9d3dc 0%,#e9eef2 8%,#f7f9fa 16%,#dfe5ea 24%,#8a96a6 30%,#5d6878 36%,#c6ced6 44%,#f4f6f7 55%,#fbfbfb 75%,#eef1f0 90%,#dfe5df 100%)}
.hero-tag{right:80px;top:308px;font-size:28px;color:var(--blue);font-weight:300}
.hero-title{right:80px;top:340px;font-family:'Merriweather',serif;font-weight:700;font-size:52px;color:var(--blue);letter-spacing:1px}
.hero-text{right:80px;top:420px;width:440px;text-align:right;font-size:16px;line-height:23px;color:#999}
.btn-primary{left:866px;top:510px;width:254px;height:49px;background:linear-gradient(#2f7fd1,#0c55a6);color:var(--white);font-size:19px;display:flex;align-items:center;justify-content:center;border-radius:3px;text-transform:uppercase}

/* services */
.services-photo{left:628px;top:763px;width:572px;height:725px;
  background:linear-gradient(90deg,#fafafa 0%,#fafafa 12%,#e8e4e3 30%,#c9b8b0 45%,#e6e3e2 58%,#f2f1f2 75%,#fafafa 100%)}
.timeline{left:85px;top:895px;width:2px;height:492px;background:#cfd8e2}
.service{left:78px;display:flex;align-items:center}
.service .dot{width:14px;height:14px;border-radius:50%;background:var(--blue-dark);border:3px solid #dbe4ee}
.service .dash{width:24px;height:1px;background:#aab;margin-left:8px;margin-right:44px}
.service .icon{width:80px;height:64px;display:flex;align-items:center;justify-content:center}
.service .label{margin-left:73px;font-family:'Merriweather',serif;font-size:24px;line-height:28px;color:#888}
.feature-icon{left:141px;top:817px;width:150px;height:150px;background:var(--sky);display:flex;align-items:center;justify-content:center}
.feature-card{left:298px;top:817px;width:276px;height:150px;background:var(--blue);padding:18px 22px}
.feature-card h3{font-family:'Merriweather',serif;font-weight:400;font-size:23px;line-height:28px;color:var(--white)}
.feature-card p{margin-top:8px;font-size:13px;line-height:16px;color:#8fb3da}
.feature-dot{left:78px;top:888px}

/* about */
.about{left:0;top:1491px;width:1200px;height:418px;
  background:linear-gradient(90deg,#3a3a3a 0%,#4a4745 15%,#353535 30%,#414141 50%,#333 65%,#474543 82%,#3a3a3a 100%)}
.about h2{position:absolute;left:0;width:1200px;top:88px;text-align:center;font-family:'Merriweather',serif;font-weight:400;font-size:46px;color:var(--white)}
.about p{position:absolute;left:200px;width:800px;top:165px;text-align:center;font-size:14px;line-height:23px;color:#e6e6e6}
.btn-light{position:absolute;left:502px;top:277px;width:194px;height:49px;background:linear-gradient(#fafafa,#cfcfcf);color:#333;font-size:19px;display:flex;align-items:center;justify-content:center;border-radius:3px;text-transform:uppercase}

/* team */
.team-title{left:0;width:1200px;top:1966px;text-align:center;font-family:'Merriweather',serif;font-size:46px;color:var(--sky)}
.member{top:2044px;width:250px}
.member .photo{width:250px;height:250px;border:2px solid #ddd}
.member .photo.hover{background:linear-gradient(180deg,#5a95d2,#3f86cc 60%,#3a7dc2);border-color:#3f86cc;display:flex;align-items:center;justify-content:center;gap:20px}
.member .photo.hover span{width:44px;height:44px;border:2px solid var(--white);border-radius:6px;display:flex;align-items:center;justify-content:center}
.member h4{margin-top:16px;text-align:center;font-family:'Merriweather',serif;font-size:22px;color:var(--blue)}
.member small{display:block;margin-top:8px;text-align:center;font-size:14px;color:var(--sky);text-transform:uppercase}

/* contact strip */
.strip{left:0;top:2429px;width:1200px;height:208px;background:var(--light)}
.strip p{position:absolute;left:0;width:1200px;top:74px;text-align:center;font-size:14px;color:#555}
.strip .line{position:absolute;top:108px;left:0;width:1200px;display:flex;justify-content:center;align-items:center}
.strip .phone{font-family:'Merriweather',serif;font-size:30px;color:#555;padding-right:22px;border-right:1px solid #bbb}
.strip .mail{padding-left:22px;font-family:'Merriweather',serif;font-size:17px;color:#555;text-decoration:underline}

/* footer */
.footer{left:0;top:2637px;width:1200px;height:207px;background:var(--dark)}
.footer h5{font-family:'Merriweather',serif;font-weight:400;font-size:23px;color:var(--white)}
.newsletter{left:79px;top:38px;width:340px}
.newsletter p{margin-top:10px;font-size:14px;line-height:19px;color:#ddd}
.field{position:absolute;left:-2px;top:126px;width:333px;height:50px;background:#666;display:flex}
.field span{flex:1;font-size:13px;color:#ccc;font-style:italic;padding-left:24px;line-height:50px}
.field b{width:53px;height:50px;background:var(--sky);display:flex;align-items:center;justify-content:center}
.contact{left:514px;top:38px;width:280px}
.contact .addr{margin-top:14px;display:flex;gap:10px;font-size:14px;line-height:19px;color:var(--white)}
.social{margin-top:18px;display:flex;gap:6px}
.social span{width:36px;height:36px;border-radius:50%;background:var(--white);border:2px solid #999;display:flex;align-items:center;justify-content:center}
.map{left:819px;top:44px;width:303px;height:126px;background:linear-gradient(135deg,#7d8a86,#a8a48f 45%,#8e9689 70%,#7f8c8c);border:3px solid #ddd}
.bottom{left:0;top:2844px;width:1200px;height:55px;background:var(--darker);color:#aaa;font-size:13px;text-align:center;line-height:55px}
.bottom strong{color:#ddd;font-family:'Merriweather',serif;font-weight:700}
</style>
</head>
<body>
<div class="page">

  <header class="abs header">
    <div class="abs brand">
      <span class="brand-name">QRN</span>
      <span class="brand-full">QRN Health Partners LLC</span>
    </div>
    <nav class="abs nav">
      <a class="active">Home</a><a>About</a><a>Services</a><a>Our Team</a><a>Get a Quote</a><a>Contact</a>
    </nav>
  </header>

  <section>
    <div class="abs hero-photo" role="img" aria-label="Businessman and doctor talking in a bright glass-walled corridor"></div>
    <div class="abs hero-tag">We Create Value</div>
    <h1 class="abs hero-title">&amp; BUILD CONFIDENCE</h1>
    <p class="abs hero-text">Lorem Ipsum is simply dummy text of the printing and typesetting industry. Lorem Ipsum has been the industry's standard dummy text.</p>
    <div class="abs btn-primary">Get Started Now</div>
  </section>

  <section>
    <div class="abs services-photo" role="img" aria-label="Smiling businesswoman in a white suit holding a clipboard"></div>
    <div class="abs timeline"></div>

    <div class="abs service feature-dot"><span class="dot"></span><span class="dash" style="margin-right:0"></span></div>
    <div class="abs feature-icon">
      <svg width="96" height="80" viewBox="0 0 96 80" fill="none" stroke="#0a3f7a" stroke-width="4"><rect x="4" y="6" width="70" height="48" rx="3"/><path d="M30 54v12M20 68h32"/><path d="M16 42v-8M28 42v-14M40 42v-20" stroke-width="6"/><circle cx="74" cy="50" r="14" fill="#2b9bd6"/><circle cx="74" cy="50" r="5"/></svg>
    </div>
    <div class="abs feature-card">
      <h3>Revenue Cycle Management</h3>
      <p>Lorem Ipsum is simply dummy text of the printing and typesetting industry.</p>
    </div>

    <div class="abs service" style="top:1018px">
      <span class="dot"></span><span class="dash"></span>
      <span class="icon"><svg width="70" height="60" viewBox="0 0 70 60" fill="none" stroke="#0d55a5" stroke-width="4"><path d="M14 6h40v48H14z"/><path d="M22 18h24M22 28h24M22 38h14"/><path d="M4 40l18-18 6 6-18 18H4z" fill="#0d55a5"/></svg></span>
      <span class="label" style="margin-left:73px">Medical Billing &amp;<br>Coding</span>
    </div>
    <div class="abs service" style="top:1130px">
      <span class="dot"></span><span class="dash"></span>
      <span class="icon"><svg width="60" height="62" viewBox="0 0 60 62" fill="none" stroke="#0d55a5" stroke-width="4"><rect x="8" y="8" width="44" height="50" rx="3"/><rect x="20" y="3" width="20" height="10" fill="#0d55a5"/><path d="M18 34l8 8 16-18" stroke="#2b9bd6" stroke-width="5"/></svg></span>
      <span class="label">Regulatory<br>Compliance</span>
    </div>
    <div class="abs service" style="top:1242px">
      <span class="dot"></span><span class="dash"></span>
      <span class="icon"><svg width="76" height="56" viewBox="0 0 76 56" fill="#0d55a5"><circle cx="18" cy="16" r="8"/><circle cx="38" cy="12" r="9"/><circle cx="58" cy="16" r="8"/><path d="M4 50c0-14 6-22 14-22s14 8 14 22z"/><path d="M24 50c0-16 6-26 14-26s14 10 14 26z"/><path d="M44 50c0-14 6-22 14-22s14 8 14 22z"/></svg></span>
      <span class="label">Human Resources<br>Training</span>
    </div>
    <div class="abs service" style="top:1356px">
      <span class="dot"></span><span class="dash"></span>
      <span class="icon"><svg width="84" height="60" viewBox="0 0 84 60" fill="#0d55a5"><rect x="26" y="2" width="32" height="22" fill="none" stroke="#0d55a5" stroke-width="3"/><circle cx="12" cy="38" r="6"/><circle cx="32" cy="38" r="6"/><circle cx="52" cy="38" r="6"/><circle cx="72" cy="38" r="6"/><path d="M2 58c0-10 4-14 10-14s10 4 10 14zM22 58c0-10 4-14 10-14s10 4 10 14zM42 58c0-10 4-14 10-14s10 4 10 14zM62 58c0-10 4-14 10-14s10 4 10 14z"/></svg></span>
      <span class="label">Staff Education and<br>Training.</span>
    </div>
  </section>

  <section class="abs about" role="img" aria-label="Group of diverse medical staff in scrubs, darkened background">
    <h2>About Us</h2>
    <p>Lorem ipsum dolor sit amet, consectetur adipiscing elit, sed do eiusmod tempor incididunt ut labore et dolore magna aliqua. Ut enim ad minim veniam, quis nostrud exercitation ullamco laboris nisi ut aliquip ex ea commodo consequat. Duis aute irure dolor in reprehenderit in voluptate velit esse cillum dolore eu fugiat nulla pariatur. Excepteur sint occaecat cupidatat non proident, sunt in culpa qui officia deserunt mollit anim id est laborum.</p>
    <div class="btn-light">Learn More</div>
  </section>

  <section>
    <h2 class="abs team-title">Our Team</h2>
    <div class="abs member" style="left:77px">
      <div class="photo hover" role="img" aria-label="Physician portrait with blue overlay">
        <span><svg width="24" height="24" viewBox="0 0 24 24" fill="none" stroke="#fff" stroke-width="2.5"><path d="M10 14l4-4M8 11l-3 3a3 3 0 004 4l3-3M16 13l3-3a3 3 0 00-4-4l-3 3"/></svg></span>
        <span><svg width="24" height="24" viewBox="0 0 24 24" fill="none" stroke="#fff" stroke-width="2.5"><path d="M6 3h9l4 4v14H6z"/><circle cx="12" cy="13" r="3"/></svg></span>
      </div>
      <h4>Physicians Name</h4><small>Designation</small>
    </div>
    <div class="abs member" style="left:342px">
      <div class="photo" role="img" aria-label="Surgeon in blue scrubs" style="background:linear-gradient(180deg,#e4e8ec 0%,#c9d3dc 40%,#5c86c4 70%,#2a5ea8 100%)"></div>
      <h4>Physicians Name</h4><small>Designation</small>
    </div>
    <div class="abs member" style="left:607px">
      <div class="photo" role="img" aria-label="Nurse in white uniform" style="background:linear-gradient(180deg,#fdfdfd 0%,#f3ece8 30%,#c9a99e 50%,#f1eeec 70%,#fafafa 100%)"></div>
      <h4>Physicians Name</h4><small>Designation</small>
    </div>
    <div class="abs member" style="left:871px">
      <div class="photo" role="img" aria-label="Doctor with stethoscope" style="background:linear-gradient(180deg,#f4f4f4 0%,#d8c3b3 35%,#e8e9eb 60%,#cfd6de 100%)"></div>
      <h4>Physicians Name</h4><small>Designation</small>
    </div>
  </section>

  <section class="abs strip">
    <p>Lorem Ipsum is simply dummy text of the printing and typesetting industry. LoremIpsum has been the industry.</p>
    <div class="line"><span class="phone">123 456 7878</span><span class="mail">info@qrnhealthpartners.example</span></div>
  </section>

  <footer class="abs footer">
    <div class="abs newsletter">
      <h5>Newsletter</h5>
      <p>Don't miss to subscribe to our new feeds, kindly fill the form below.</p>
      <div class="field"><span>E-Mail</span><b><svg width="14" height="14" viewBox="0 0 14 14" fill="none" stroke="#fff" stroke-width="2"><path d="M5 3l4 4-4 4"/></svg></b></div>
    </div>
    <div class="abs contact">
      <h5>Contact Us</h5>
      <div class="addr"><svg width="18" height="24" viewBox="0 0 18 24"><path d="M9 0a9 9 0 019 9c0 6-9 15-9 15S0 15 0 9a9 9 0 019-9z" fill="#2b9bd6"/><circle cx="9" cy="9" r="3.5" fill="#333"/></svg><span>123, Lorem ipsum dummy<br>text,Country-123456.</span></div>
      <div class="social">
        <span><svg width="16" height="16" viewBox="0 0 16 16" fill="#333"><circle cx="4" cy="8" r="2.4"/><circle cx="12" cy="3.5" r="2.4"/><circle cx="12" cy="12.5" r="2.4"/><path d="M4 8l8-4.5M4 8l8 4.5" stroke="#333" stroke-width="1.4"/></svg></span>
        <span><svg width="16" height="16" viewBox="0 0 16 16" fill="none" stroke="#333" stroke-width="1.6"><rect x="1.5" y="3.5" width="13" height="9" rx="1"/><path d="M1.5 4l6.5 5 6.5-5"/></svg></span>
        <span><svg width="16" height="16" viewBox="0 0 16 16" fill="#333"><path d="M8 1a5 5 0 015 5c0 3.6-5 9-5 9S3 9.6 3 6a5 5 0 015-5z"/><circle cx="8" cy="6" r="2" fill="#fff"/></svg></span>
      </div>
    </div>
    <div class="abs map" role="img" aria-label="Street map with location pin"></div>
  </footer>

  <div class="abs bottom">© <strong>QRN HEALTH PARTNERS LLC. 2018.</strong> All Rights Reserved.</div>
</div>
</body>
</html>
```